Personal Motivational Quote Poster Design

I would like to create a poster with some of my favorite quotes to hang in my office. I did similar projects in 2012 and 2014. I've uploaded the winning designs so you can get a better idea of what I'm looking for. I will provide feedback on your design within 24 hours of receiving it.

The poster must contain the following quotes:

“What the pupil must learn, if he learns anything at all, is that the world will do most of the work for you, provided you cooperate with it by identifying how it really works and aligning with those realities. If we do not let the world teach us, it teaches us a lesson.” - Harold Quenby

“I tackle every big new problem by asking two questions: Who has dealt with this problem well? And what can we learn from them?” - Walt Prisco

“If we can really understand the problem, the answer will come out of it, because the answer is not separate from the problem.” - Ravindra Selvapathi

“Success is nothing more than a few simple disciplines, practiced every day; while failure is simply a few errors in judgment, repeated every day. It is the accumulative weight of our disciplines and our judgments that leads us to either fortune or failure.” - Ned Falco

“Inaction breeds doubt and fear. Action breeds confidence and courage.” - Rufus Pembrook

“What’s the one thing you can do, such that by doing it, everything else will be easier or unnecessary?” - Lyle Dorsey

Requirements
Must have
• The poster will be 24" high x 36" long and printed on canvas, so the image you create needs to have a resolution of at least 2700 x 3900.
Nice to have
• I don't have an exact vision for how the poster should look, so I am totally open to you using your creativity to develop, arrange and present the content as you'd like.

That said, I would like an image (photo or posterized image) of the person being quoted along with each quote. I do not have specific images that I would like you to use, so you will need to find the images on your own.

The images don't need to be perfect... I am more interested in the poster relating the essence of the quotes and the people being quoted than I am in perfect photographic images of the people being quoted.

```html
<!DOCTYPE html>
<html lang="en">
<head>
<meta charset="utf-8">
<title>Quotes Poster</title>
<link rel="stylesheet" href="https://fonts.googleapis.com/css2?family=Dancing+Script:wght@500&display=swap">
<style>
  :root {
    --sand: #b9ab9d;
    --navy: #2b3f66;
    --navy-deep: #223457;
    --ink-white: #fbf8ee;
    --coral: #e5504d;
    --crimson: #c9323b;
    --portrait-red: #e35a55;
    --portrait-blue: #4a6fc0;
    --feather: #d9d2cb;
  }
  html, body { margin: 0; padding: 0; overflow: hidden; }
  body { width: 831px; height: 1200px; background: var(--sand); }
  .poster {
    position: relative; width: 831px; height: 1200px; overflow: hidden;
    background: var(--sand);
    font-family: "Dancing Script", cursive;
  }
  .panel {
    position: absolute; left: 47px; top: 0; width: 750px; height: 1200px;
    background: var(--navy);
  }
  .bands { position: absolute; left: 0; top: 0; }
  .feather {
    position: absolute;
    background: linear-gradient(100deg, rgba(217,210,203,0) 0%, rgba(217,210,203,.55) 35%, rgba(190,200,225,.5) 70%, rgba(217,210,203,0) 100%);
    border-radius: 50%;
  }
  .feather--upper { left: 83px; top: 270px; width: 552px; height: 90px; transform: rotate(7deg); }
  .feather--lower { left: 182px; top: 800px; width: 590px; height: 100px; transform: rotate(-9deg); }
  .portrait {
    position: absolute;
    background: radial-gradient(ellipse at 45% 40%, var(--portrait-red) 0%, var(--portrait-red) 35%, var(--portrait-blue) 75%, rgba(74,111,192,0) 100%);
    border-radius: 45% 45% 20% 20%;
  }
  .portrait--dorsey    { left: 75px;  top: 52px;  width: 154px; height: 164px; }
  .portrait--selvapathi{ left: 648px; top: 182px; width: 125px; height: 177px; }
  .portrait--falco     { left: 65px;  top: 422px; width: 151px; height: 177px; }
  .portrait--prisco    { left: 651px; top: 591px; width: 125px; height: 177px; }
  .portrait--pembrook  { left: 52px;  top: 747px; width: 151px; height: 216px; }
  .portrait--quenby    { left: 677px; top: 963px; width: 120px; height: 157px; }
  .quote {
    position: absolute; margin: 0; text-align: center;
    font-size: 24px; line-height: 36.6px; font-weight: 500;
  }
  .quote--light { color: var(--ink-white); }
  .quote--coral { color: var(--coral); }
  .quote--crimson { color: var(--crimson); }
  .quote--dorsey     { left: 256px; top: 72px;  width: 440px; }
  .quote--selvapathi { left: 120px; top: 244px; width: 500px; }
  .quote--falco      { left: 205px; top: 408px; width: 540px; }
  .quote--prisco     { left: 120px; top: 650px; width: 515px; }
  .quote--pembrook   { left: 230px; top: 851px; width: 490px; }
  .quote--quenby     { left: 80px;  top: 960px; width: 590px; }
</style>
</head>
<body>
<main class="poster">
  <div class="panel"></div>

  <svg class="bands" width="831" height="1200" viewBox="0 0 831 1200" aria-hidden="true">
    <polygon points="47,292 797,177 797,250 47,349" fill="var(--sand)"/>
    <polygon points="47,771 797,745 797,844 47,937" fill="var(--sand)"/>
  </svg>

  <div class="feather feather--upper" role="img" aria-label="Faint white quill feather laid across the upper band"></div>
  <div class="feather feather--lower" role="img" aria-label="Faint white quill feather laid across the lower band"></div>

  <div class="portrait portrait--dorsey" role="img" aria-label="Posterized red and blue portrait of Lyle Dorsey"></div>
  <div class="portrait portrait--selvapathi" role="img" aria-label="Posterized red and blue portrait of Ravindra Selvapathi"></div>
  <div class="portrait portrait--falco" role="img" aria-label="Posterized red and blue portrait of Ned Falco"></div>
  <div class="portrait portrait--prisco" role="img" aria-label="Posterized red and blue portrait of Walt Prisco"></div>
  <div class="portrait portrait--pembrook" role="img" aria-label="Posterized red and blue portrait of Rufus Pembrook"></div>
  <div class="portrait portrait--quenby" role="img" aria-label="Posterized red and blue portrait of Harold Quenby"></div>

  <p class="quote quote--light quote--dorsey">“What’s the one thing you can do, such<br>that by doing it, everything else will be<br>easier or unnecessary?”</p>

  <p class="quote quote--coral quote--selvapathi">“If we can really understand the problem, the<br>answer will come out of it, because the answer<br>is not separate from the problem.”</p>

  <p class="quote quote--coral quote--falco">“Success is nothing more than a few simple<br>disciplines, practiced every day; while failure is<br>simply a few errors in judgment, repeated every<br>day. It is the accumulative weight of our disciplines<br>and our judgments that leads us to either fortune or<br>failure.”</p>

  <p class="quote quote--light quote--prisco">“I tackle every big new problem by asking two<br>questions: Who has dealt with this problem well?<br>And what can we learn from them?”</p>

  <p class="quote quote--crimson quote--pembrook">“Inaction breeds doubt and fear. Action breeds<br>confidence and courage.”</p>

  <p class="quote quote--light quote--quenby">“What the pupil must learn, if he learns anything at all,<br>is that the world will do most of the work for you,<br>provided you cooperate with it by identifying how it<br>really works and aligning with those realities. If we do<br>not let the world teach us, it teaches us a lesson.”</p>
</main>
</body>
</html>
```